Las Vegas transportation company needs a dynamic design for business cards

We are a transportation management company based in Las Vegas specializing in operating and maintaining public transit systems. We want to keep our existing logo but would like to design business cards that feature one or more transit systems (e.g. monorail, train, bus) and maybe also the Las Vegas landscape.

```html
<!DOCTYPE html>
<html lang="en">
<head>
<meta charset="utf-8">
<title>Meridian Management Group – Business Card</title>
<link href="https://fonts.googleapis.com/css2?family=Cinzel:wght@500;600&family=Lato:wght@300;400&display=swap" rel="stylesheet">
<style>
  :root {
    --navy: #13296b;
    --sky: #9dbfe8;
    --ink: #1d1d22;
    --rule: #9a9a9a;
    --paper: #ffffff;
    --backdrop: #2a2a2c;
  }
  * { box-sizing: border-box; margin: 0; padding: 0; }
  html, body { width: 1200px; height: 1108px; overflow: hidden; }
  body {
    background: var(--backdrop);
    display: flex;
    align-items: center;
    justify-content: center;
    gap: 60px;
    font-family: "Lato", Arial, sans-serif;
  }
  .card {
    width: 440px;
    height: 770px;
    border-radius: 22px;
    overflow: hidden;
    position: relative;
  }
  .card-front {
    background: var(--paper);
    display: flex;
    flex-direction: column;
    align-items: center;
    padding-top: 150px;
  }
  .brand {
    display: flex;
    align-items: center;
    gap: 14px;
    color: var(--navy);
    font-family: "Cinzel", Georgia, serif;
    font-weight: 500;
  }
  .brand-mark {
    width: 20px; height: 20px;
    border-radius: 50%;
    background: var(--navy);
  }
  .brand-name { font-size: 46px; letter-spacing: 1px; line-height: 1; }
  .brand-sub {
    margin-top: 12px;
    font-family: "Lato", Arial, sans-serif;
    font-weight: 300;
    color: var(--sky);
    font-size: 17px;
    letter-spacing: 5px;
  }
  .person {
    margin-top: 150px;
    text-align: center;
  }
  .person-name {
    font-family: "Cinzel", Georgia, serif;
    font-weight: 600;
    color: var(--navy);
    font-size: 30px;
    letter-spacing: 1px;
  }
  .person-title {
    margin-top: 4px;
    font-size: 21px;
    color: var(--ink);
  }
  .icon-row {
    margin-top: 24px;
    width: 300px;
    display: flex;
    align-items: center;
    gap: 8px;
  }
  .icon-row .rule { flex: 1; height: 1px; background: var(--rule); }
  .icon {
    width: 32px; height: 32px;
    background: var(--navy);
    border-radius: 4px;
    display: flex; align-items: center; justify-content: center;
  }
  .icon svg { width: 20px; height: 20px; }
  .contact {
    margin-top: 16px;
    text-align: center;
    font-size: 21px;
    line-height: 1.35;
    color: var(--ink);
  }
  .divider { margin-top: 14px; width: 300px; height: 1px; background: var(--rule); }
  .address {
    margin-top: 14px;
    text-align: center;
    font-size: 21px;
    line-height: 1.35;
    color: var(--ink);
  }
  .card-back {
    background: #111;
    display: grid;
    grid-template-rows: 50% 17% 19% 14%;
    gap: 4px;
  }
  .scene { width: 100%; height: 100%; }
  .scene-skyline {
    background: linear-gradient(180deg, #0c0a10 0%, #1a1418 35%, #6a4a1c 62%, #c9962e 75%, #3a2118 88%, #b8303a 100%);
  }
  .scene-buses {
    background: linear-gradient(90deg, #7b8fa8 0%, #8c2f6a 30%, #b82a3a 55%, #d8262a 75%, #c9ccd2 100%);
  }
  .scene-train {
    background: linear-gradient(90deg, #eef0f3 0%, #dcdfe4 35%, #a53a30 60%, #c24a3a 80%, #e6e8ec 100%);
  }
  .scene-monorail {
    background: linear-gradient(180deg, #a9c6e6 0%, #dfe7ef 45%, #f2f3f4 60%, #6fbf4a 70%, #e9ebee 80%, #8d9198 100%);
  }
</style>
</head>
<body>
  <section class="card card-front">
    <div class="brand">
      <span class="brand-mark"></span>
      <span class="brand-name">MERIDIAN</span>
    </div>
    <div class="brand-sub">MANAGEMENT GROUP</div>

    <div class="person">
      <div class="person-name">DANIEL REYES</div>
      <div class="person-title">Managing Director</div>
    </div>

    <div class="icon-row">
      <span class="rule"></span>
      <span class="icon" aria-label="Phone">
        <svg viewBox="0 0 24 24" fill="#fff"><path d="M6.6 10.8a15.1 15.1 0 0 0 6.6 6.6l2.2-2.2a1 1 0 0 1 1-.25 11.4 11.4 0 0 0 3.6.57 1 1 0 0 1 1 1V20a1 1 0 0 1-1 1A17 17 0 0 1 3 4a1 1 0 0 1 1-1h3.5a1 1 0 0 1 1 1c0 1.25.2 2.45.57 3.57a1 1 0 0 1-.25 1z"/></svg>
      </span>
      <span class="icon" aria-label="Email">
        <svg viewBox="0 0 24 24" fill="none" stroke="#fff" stroke-width="2"><rect x="3" y="5" width="18" height="14"/><path d="M3 5l9 8 9-8"/></svg>
      </span>
      <span class="icon" aria-label="Website">
        <svg viewBox="0 0 24 24" fill="none" stroke="#fff" stroke-width="1.8"><circle cx="12" cy="12" r="9"/><path d="M3 12h18M12 3c3 3.5 3 14.5 0 18M12 3c-3 3.5-3 14.5 0 18"/></svg>
      </span>
      <span class="rule"></span>
    </div>

    <div class="contact">
      <p>702-555 0148</p>
      <p>hello@meridianmg.com</p>
      <p>www.meridianmg.com</p>
    </div>
    <div class="divider"></div>
    <div class="address">
      <p>1850 Desert Rail Way</p>
      <p>89109, Nevada USA</p>
    </div>
  </section>

  <section class="card card-back">
    <div class="scene scene-skyline" role="img" aria-label="Las Vegas Strip at night with tower, hotels and light trails"></div>
    <div class="scene scene-buses" role="img" aria-label="Red double-decker buses in the city"></div>
    <div class="scene scene-train" role="img" aria-label="Red train crossing a snowy landscape"></div>
    <div class="scene scene-monorail" role="img" aria-label="White and green monorail on an elevated track"></div>
  </section>
</body>
</html>
```